Website for Architecture & Interior Design firm

We are architecture and interior design firm looking for website design, word press based, smooth, elegant and easy to use for visitors. It should be easy to navigate using a mobile phone, with the ability to change pictures easily. It is a Bilingual website, (English: left to right, Arabic: right to left). A button in the menu bar is required to change the language, At first, we expect an English version, then we will help the designer by providing Arabic translation for any part of the website. Our website main purpose is to display our works in a picture format (Portfolio) to our clients, which mainly consist of four galleries from our (Services) as follow: 1- Architecture 2- Interior Design 3- Project Management 4- Importing from Abroad - Each service will have its page, which displays projects(items) in thumbnail format with simple text, which deploys (when clicked) into Fullscreen gallery to show the items related pictures (Dark gray or black background). - Navigation buttons/arrows are required, (X) button to close the navigation. - This is a very important part, the user experience in PC/Browser mode or Mobile mode should be easy, error-free and fast. Our homepage consists of four main elements: A- Edge to edge picture (Changing in a smooth transitional way, Random pictures from our Services) with our Logo, also persistent menu bar in the top (Home | About Us | Architecture | Interior design | Project Management | Importing from Abroad) + Social media icons B- Photo tiles (Random pictures from our Services) C- Our Services in a fixed 4-tile picture (Clickable) D- Contact Section (Simple name, contact number, message form) We expect the final service should be: 1- a fully functioning website, WordPress based, ready to be used by visitors 2- full content filling, we will contact the designer and provide the material (texture, text,etc..)
Colors
Designer to choose colors to be used in the design.
Look and feel
Each slider illustrates characteristics of the customer's brand and the style your logo design should communicate.

```html
<!DOCTYPE html>
<html lang="en">
<head>
<meta charset="utf-8">
<title>R &amp; R Studios</title>
<link rel="stylesheet" href="https://fonts.googleapis.com/css2?family=Roboto:wght@300;400;500;700;900&display=swap">
<style>
  :root {
    --navy: #1d1b3c;
    --navy-deep: #27223f;
    --gold-dark: #a4742c;
    --gold-light: #d8a948;
    --gold-text: #b07a2d;
    --ink: #222222;
    --white: #ffffff;
    --tile-band: rgba(20, 22, 48, 0.75);
  }
  * { box-sizing: border-box; margin: 0; padding: 0; }
  html, body { width: 1200px; height: 3333px; overflow: hidden; }
  body { position: relative; background: var(--white); font-family: "Roboto", Arial, sans-serif; color: var(--ink); }
  .abs { position: absolute; }

  /* Hero */
  .hero { left: 0; top: 0; width: 1200px; height: 712px;
    background: linear-gradient(180deg, #3f3b6e 0%, #2c2a52 30%, #2b2440 60%, #3a2a2c 85%, #2a2236 100%); }
  .hero-glow { left: 0; top: 0; width: 1200px; height: 712px;
    background: radial-gradient(ellipse 500px 260px at 300px 520px, rgba(214,140,60,0.35), transparent 70%),
                radial-gradient(ellipse 420px 240px at 880px 560px, rgba(190,110,70,0.25), transparent 70%); }
  .logo { color: var(--white); line-height: 1; }
  .logo .top { display: block; font-weight: 700; font-size: 34px; letter-spacing: 1px; }
  .logo .bottom { display: block; font-weight: 300; font-size: 34px; letter-spacing: 0.5px; margin-top: 2px; }
  .main-nav { left: 277px; top: 69px; display: flex; gap: 27px; font-size: 14px; font-weight: 500; color: var(--white); }
  .main-nav .active { color: var(--gold-light); position: relative; }
  .main-nav .active::after { content: ""; position: absolute; left: 0; right: 0; top: 24px; height: 3px; background: var(--white); }
  .social { display: flex; gap: 34px; }
  .social span { width: 16px; height: 16px; border-radius: 50%; display: block; }
  .hero .social { left: 842px; top: 25px; }
  .hero .social span { background: var(--white); }
  .lang { left: 1039px; top: 17px; width: 82px; height: 32px; border: 1px solid rgba(255,255,255,0.7);
    color: var(--white); font-size: 13px; display: flex; align-items: center; justify-content: center; gap: 4px; }
  .welcome { left: 0; width: 1200px; top: 262px; text-align: center; color: var(--white); font-weight: 300; font-size: 44px; }
  .hero-title { left: 0; width: 1200px; top: 318px; text-align: center; color: var(--white); font-weight: 900; font-size: 80px; letter-spacing: 1px; }
  .btn { background: linear-gradient(90deg, var(--gold-dark), var(--gold-light)); color: var(--white);
    font-weight: 700; display: flex; align-items: center; justify-content: center; }
  .hero-btn { left: 492px; top: 417px; width: 207px; height: 51px; font-size: 19px; }
  .arrow { top: 343px; }
  .notch { left: 0; top: 650px; }

  /* About */
  .about-photo { left: 124px; top: 725px; }
  .section-title { font-weight: 700; font-size: 36px; color: var(--navy); }
  .rule { height: 4px; background: var(--navy); }
  .about-text { left: 589px; width: 520px; font-size: 17px; line-height: 27px; color: var(--ink); }
  .about-btn { left: 584px; top: 1071px; width: 186px; height: 49px; font-size: 18px; }

  /* Services */
  .centered { left: 0; width: 1200px; text-align: center; }
  .tile { top: 1370px; height: 293px; }
  .tile-band { position: absolute; left: 0; right: 0; bottom: 0; height: 64px; background: var(--tile-band);
    color: var(--white); font-weight: 700; font-size: 22px; display: flex; align-items: center; justify-content: center;
    text-align: center; line-height: 27px; }
  .tile-featured { left: 604px; top: 1352px; width: 294px; height: 326px;
    background: linear-gradient(160deg, #d9a645, #c99038 60%, #d3a456); }
  .tile-featured .label { position: absolute; left: 0; right: 0; top: 120px; text-align: center; color: var(--white);
    font-weight: 700; font-size: 24px; line-height: 31px; }
  .tile-featured .outline-btn { position: absolute; left: 72px; top: 200px; width: 151px; height: 40px;
    border: 2px solid var(--white); color: var(--white); font-weight: 500; font-size: 16px;
    display: flex; align-items: center; justify-content: center; }

  /* Gallery */
  .gallery-title { color: var(--gold-text); }

  /* Contact */
  .contact { left: 0; top: 2406px; width: 1200px; height: 697px;
    background: linear-gradient(180deg, #2a2643 0%, #262140 60%, #1e1a33 100%); }
  .contact-title { color: var(--white); }
  .field { background: var(--white); font-size: 17px; color: #555; padding: 0 20px; display: flex; align-items: center; }
  .field.message { align-items: flex-start; padding-top: 22px; }
  .submit { left: 505px; top: 2945px; width: 207px; height: 52px; font-size: 19px; }

  /* Footer */
  .footer-logo { color: var(--navy); }
  .footer-logo .top, .footer-logo .bottom { font-size: 42px; }
  .footer-links { font-size: 13px; font-weight: 700; color: var(--navy); line-height: 26px; list-style: none; }
  .footer .social span { background: var(--navy); }
  .legal { font-size: 13px; color: var(--navy); line-height: 26px; }
</style>
</head>
<body>

<header class="hero abs">
  <div class="hero-glow abs" role="img" aria-label="Night skyline of a city with a tall arched tower and glowing streets"></div>
  <div class="logo abs" style="left:62px;top:32px;">
    <span class="top">R &amp; R</span><span class="bottom">STUDIOS</span>
  </div>
  <nav class="main-nav abs">
    <span class="active">HOME</span><span>ABOUT US</span><span>ARCHITECTURE</span><span>INTERIOR DESIGN</span><span>PROJECT MANAGEMENT</span><span>IMPORTING FROM ABROAD</span>
  </nav>
  <div class="social abs"><span></span><span></span><span></span><span></span></div>
  <div class="lang abs">ENG
    <svg width="14" height="10" viewBox="0 0 14 10"><path d="M1 2 L7 8 L13 2" fill="none" stroke="#fff" stroke-width="1.6"/></svg>
  </div>
  <div class="welcome abs">WELCOME TO</div>
  <h1 class="hero-title abs">R &amp; R STUDIOS</h1>
  <div class="btn hero-btn abs">GET STARTED</div>
  <svg class="arrow abs" style="left:88px;" width="26" height="60" viewBox="0 0 26 60"><path d="M24 2 L3 30 L24 58" fill="none" stroke="#fff" stroke-opacity="0.8" stroke-width="2"/></svg>
  <svg class="arrow abs" style="left:1112px;" width="26" height="60" viewBox="0 0 26 60"><path d="M2 2 L23 30 L2 58" fill="none" stroke="#fff" stroke-opacity="0.8" stroke-width="2"/></svg>
  <svg class="notch abs" width="1200" height="62" viewBox="0 0 1200 62"><polygon points="228,62 326,6 427,62" fill="#fff"/></svg>
</header>

<section class="about">
  <svg class="about-photo abs" width="404" height="466" viewBox="0 0 404 466" role="img" aria-label="Hands drafting an architectural floor plan with ruler and pen">
    <defs>
      <linearGradient id="planTone" x1="0" y1="0" x2="1" y2="1">
        <stop offset="0" stop-color="#e4e4e4"/><stop offset="0.55" stop-color="#c9ccd0"/><stop offset="1" stop-color="#8fa7b8"/>
      </linearGradient>
    </defs>
    <polygon points="202,0 404,116 404,350 202,466 0,350 0,116" fill="url(#planTone)"/>
  </svg>
  <h2 class="section-title abs" style="left:590px;top:798px;">ABOUT US</h2>
  <div class="rule abs" style="left:590px;top:850px;width:79px;"></div>
  <p class="about-text abs" style="top:875px;">Fusce tellus Sed metus augue convallis et vehicula ut pulvinar eu ante Integer orci tellus tristique vitae consequat nec</p>
  <p class="about-text abs" style="top:956px;">Aorta vel lectus Nulla sit amet enim Proin dui lectus cursus eu mattis laoreet viverra sit amet quam Curabitur vel dolor ultrices ipsum dictum tristique Praesent vitae lacus Ut velit e</p>
  <div class="btn about-btn abs">LEARN MORE</div>
</section>

<section class="services">
  <h2 class="section-title centered abs" style="top:1270px;">OUR SERVICES</h2>
  <div class="rule abs" style="left:558px;top:1321px;width:80px;"></div>

  <div class="tile abs" style="left:0;width:295px;background:linear-gradient(135deg,#c9c2b8,#8c8a90 50%,#2f62b8);" role="img" aria-label="Modern building facade with sculpted metal panels under blue sky">
    <div class="tile-band">ARCHITECTURE</div>
  </div>
  <div class="tile abs" style="left:303px;width:294px;background:linear-gradient(180deg,#5c4a32,#2a2220 55%,#6a5a3c);" role="img" aria-label="Ornate arched interior hall with striped arches">
    <div class="tile-band">INTERIOR DESIGN</div>
  </div>
  <div class="tile-featured abs" role="img" aria-label="Engineers reviewing plans on a construction site">
    <div class="label">PROJECT<br>MANAGEMENT</div>
    <div class="outline-btn">CLICK HERE</div>
  </div>
  <div class="tile abs" style="left:906px;width:294px;background:linear-gradient(180deg,#3c4058,#7a5a5c 40%,#2a2c3c 70%);" role="img" aria-label="Container port with cranes at dusk">
    <div class="tile-band">IMPORTING FROM<br>ABROAD</div>
  </div>
</section>

<section class="gallery">
  <h2 class="section-title gallery-title centered abs" style="top:1765px;">OUR GALLERY</h2>
  <div class="rule abs" style="left:547px;top:1816px;width:80px;"></div>

  <div class="abs" style="left:0;top:1840px;width:387px;height:278px;background:linear-gradient(180deg,#9cb8d8,#c7b8a0 55%,#6a6a5c);" role="img" aria-label="City avenue lined with palm trees and office towers"></div>
  <div class="abs" style="left:396px;top:1840px;width:396px;height:278px;background:linear-gradient(160deg,#c2a878,#3a5868 50%,#5a98c8);" role="img" aria-label="Triangulated glass canopy on a modern building"></div>
  <div class="abs" style="left:802px;top:1840px;width:398px;height:278px;background:radial-gradient(circle at 170px 100px,#c8e2f4 0,#b0a698 22%,#6c6460 70%,#3c3a3a);" role="img" aria-label="Spiral atrium with a round skylight"></div>
  <div class="abs" style="left:0;top:2129px;width:387px;height:277px;background:linear-gradient(180deg,#8cb4d6,#3c7a98 45%,#8a9486 80%,#4a5040);" role="img" aria-label="Glass office towers beside a palm-lined road"></div>
  <div class="abs" style="left:396px;top:2129px;width:396px;height:277px;background:linear-gradient(180deg,#d86a24,#e89440 45%,#f4d8a8);" role="img" aria-label="Long corridor of repeating orange arches"></div>
  <div class="abs" style="left:802px;top:2129px;width:398px;height:277px;background:linear-gradient(180deg,#1a1a48,#1c2450 45%,#3c8a48 75%,#2a5a34);" role="img" aria-label="Mosque with green dome and minaret at night"></div>
</section>

<section class="contact abs">
  <div class="abs" style="left:0;top:0;width:1200px;height:697px;background:linear-gradient(180deg,transparent 55%,rgba(12,10,26,0.45));" role="img" aria-label="Faint city skyline behind the contact form"></div>
</section>
<h2 class="section-title contact-title centered abs" style="top:2467px;">CONTACT US</h2>
<div class="abs" style="left:558px;top:2518px;width:80px;height:4px;background:var(--white);"></div>
<div class="centered abs" style="top:2563px;color:var(--white);font-size:21px;font-weight:500;">R &amp; R STUDIOS</div>
<div class="centered abs" style="top:2590px;color:var(--white);font-size:28px;font-weight:500;">(685) 555 0173</div>

<form>
  <div class="field abs" style="left:195px;top:2664px;width:391px;height:52px;">Name</div>
  <div class="field abs" style="left:604px;top:2664px;width:391px;height:52px;">Phone Number</div>
  <div class="field abs" style="left:195px;top:2732px;width:391px;height:51px;">Email address</div>
  <div class="field abs" style="left:604px;top:2732px;width:391px;height:51px;">Subject</div>
  <div class="field message abs" style="left:195px;top:2803px;width:800px;height:119px;">Message</div>
  <div class="btn submit abs">SUBMIT NOW</div>
</form>

<footer class="footer">
  <div class="logo footer-logo abs" style="left:171px;top:3168px;">
    <span class="top">R &amp; R</span><span class="bottom">STUDIOS</span>
  </div>
  <ul class="footer-links abs" style="left:422px;top:3165px;">
    <li>HOME</li><li>ABOUT US</li><li>ARCHITECTURE</li><li>INTERIOR DESIGN</li>
  </ul>
  <ul class="footer-links abs" style="left:612px;top:3168px;">
    <li>PROJECT MANAGEMENT</li><li>IMPORTING FROM ABROAD</li><li>CONTACT US</li>
  </ul>
  <div class="social abs" style="left:875px;top:3171px;"><span></span><span></span><span></span><span></span></div>
  <div class="legal abs" style="left:875px;top:3222px;">© 2019 Company Name<br>All right reserved &nbsp;|&nbsp; Privacy Policy</div>
</footer>

</body>
</html>
```